BOLD PINE HEATING AND COOLING

Industry/Entity Type

Hvac

Requirements
Must have
• logo
My name: Gavin Pruszynski
Phone number 555-309-4461
Text:
Furnace and AC repairs
New furnace and AC installation
Ductwork
Gas lines
Water Tanks
Tankless water heaters
Nice to have
• Profesional modern look

```html
<!DOCTYPE html>
<html lang="en">
<head>
<meta charset="utf-8">
<title>Bold Pine Heating and Cooling – Business Card</title>
<link rel="stylesheet" href="https://fonts.googleapis.com/css2?family=Montserrat:wght@400;500;600&family=Oswald:wght@600&display=swap">
<style>
  :root {
    --backdrop: #1c1c1c;
    --card: #262626;
    --card-edge: #303030;
    --brand-blue: #1f6cc4;
    --leaf-green: #6cbf3c;
    --text-light: #f2f2f2;
  }
  * { box-sizing: border-box; margin: 0; padding: 0; }
  html, body {
    width: 1200px; height: 900px; overflow: hidden;
    background: var(--backdrop);
    font-family: "Montserrat", sans-serif;
    color: var(--text-light);
  }
  .sheet {
    width: 1200px; height: 900px;
    display: flex; flex-direction: column; align-items: center; justify-content: center;
    gap: 40px;
  }
  .card {
    position: relative;
    width: 700px; height: 400px;
    background: var(--card);
    border: 1px solid var(--card-edge);
  }
  .brand-name {
    font-family: "Montserrat", sans-serif;
    font-weight: 600;
    color: var(--brand-blue);
    text-align: center;
    line-height: 1.15;
  }
  .brand-name .line-main { display: block; font-size: 44px; letter-spacing: 3px; }
  .brand-name .line-sub { display: block; font-size: 15px; letter-spacing: 2px; margin-top: 4px; }

  /* front */
  .card--front .brand-name { position: absolute; top: 95px; left: 0; right: 0; }
  .services {
    position: absolute; top: 255px; left: 0; right: 0;
    text-align: center; font-size: 16px; line-height: 1.6; letter-spacing: 0.3px;
  }
  .services .sep { color: var(--leaf-green); margin: 0 6px; }

  /* back */
  .card--back .brand-name { position: absolute; top: 70px; left: 0; right: 0; }
  .person {
    position: absolute; top: 235px; left: 40px; width: 270px; text-align: right;
  }
  .person-name {
    font-family: "Oswald", sans-serif; font-weight: 600;
    font-size: 34px; color: var(--brand-blue); text-transform: uppercase; line-height: 1.1;
  }
  .person-role { font-size: 20px; margin-top: 8px; }
  .divider {
    position: absolute; top: 232px; left: 334px; width: 2px; height: 84px;
    background: var(--leaf-green);
  }
  .contacts {
    position: absolute; top: 236px; left: 364px; list-style: none;
    font-size: 20px; line-height: 1.5;
  }
  .contacts li { display: flex; align-items: center; gap: 10px; }
  .contacts svg { width: 14px; height: 14px; flex: none; }
</style>
</head>
<body>
<main class="sheet">
  <section class="card card--front">
    <h1 class="brand-name">
      <span class="line-main">BOLD PINE</span>
      <span class="line-sub">HEATING AND COOLING</span>
    </h1>
    <p class="services">
      Furnace and AC repairs<span class="sep">|</span>New furnace and AC installation<br>
      Ductwork<span class="sep">|</span>Gas lines<span class="sep">|</span>Water Tanks<span class="sep">|</span>Tankless water heaters
    </p>
  </section>

  <section class="card card--back">
    <h2 class="brand-name">
      <span class="line-main">BOLD PINE</span>
      <span class="line-sub">HEATING AND COOLING</span>
    </h2>
    <div class="person">
      <p class="person-name">Gavin Pruszynski</p>
      <p class="person-role">Director</p>
    </div>
    <div class="divider"></div>
    <ul class="contacts">
      <li>
        <svg viewBox="0 0 16 16" aria-hidden="true"><path d="M4 1l2.5 3-1.5 2c1 2 2.5 3.5 4.5 4.5l2-1.5 3 2.5-1.5 2.5C7 15 1 9 1.5 3z" fill="var(--leaf-green)"/></svg>
        555-309-4461
      </li>
      <li>
        <svg viewBox="0 0 16 16" aria-hidden="true"><rect x="1.5" y="3.5" width="13" height="9" fill="none" stroke="var(--leaf-green)" stroke-width="1.5"/><path d="M1.5 3.5L8 9l6.5-5.5" fill="none" stroke="var(--leaf-green)" stroke-width="1.5"/></svg>
        info@boldpine-hvac.com
      </li>
      <li>
        <svg viewBox="0 0 16 16" aria-hidden="true"><circle cx="8" cy="8" r="6.5" fill="none" stroke="var(--leaf-green)" stroke-width="1.5"/><ellipse cx="8" cy="8" rx="3" ry="6.5" fill="none" stroke="var(--leaf-green)" stroke-width="1.2"/><path d="M1.5 8h13" stroke="var(--leaf-green)" stroke-width="1.2"/></svg>
        www.boldpine-hvac.com
      </li>
    </ul>
  </section>
</main>
</body>
</html>
```